corvale institute of business and technology web site

I need web site for the institute which focus on business courses and computer course it is also for vocation train for employment It is also carear development and advancement .It should have links to online study resource which free
Industry/Entity Type
Business
Number of Pages Required
1 page
Look and feel
Each slider illustrates characteristics of the customer's brand and the style your logo design should communicate.

```html
<!DOCTYPE html>
<html lang="en">
<head>
<meta charset="utf-8">
<title>Corvale Institute of Business and Technology</title>
<link href="https://fonts.googleapis.com/css2?family=Open+Sans:wght@400;600;700;800&display=swap" rel="stylesheet">
<style>
:root{
  --blue:#1f6db5;
  --blue-dark:#17457a;
  --navy:#1a2c4e;
  --navy-deep:#121f38;
  --orange:#f0692a;
  --green:#5aa52a;
  --text:#555b66;
  --heading:#1d3557;
  --white:#ffffff;
  --sky-top:#9fc0dc;
  --sky-bottom:#e4eef6;
}
*{margin:0;padding:0;box-sizing:border-box}
html,body{width:1200px;height:2948px;overflow:hidden}
body{font-family:"Open Sans",Arial,sans-serif;color:var(--text);background:var(--white);position:relative}
.site-header{position:absolute;top:0;left:0;width:1200px;height:110px;background:var(--white);display:flex;align-items:center;padding:0 70px;z-index:2}
.brand{display:flex;align-items:center;gap:14px}
.brand-mark{width:46px;height:46px;background:var(--blue-dark);border-radius:50%}
.brand-name{font-weight:800;font-size:40px;color:var(--blue-dark);letter-spacing:1px}
.brand-sub{font-size:9px;color:var(--blue-dark);font-weight:600;letter-spacing:.5px;margin-top:-4px}
.main-nav{display:flex;gap:26px;margin-left:auto;font-size:14px;font-weight:600;color:#444}
.main-nav .active{color:var(--orange)}
.phone-btn{margin-left:38px;background:var(--orange);color:var(--white);font-weight:700;font-size:15px;padding:10px 22px;border-radius:22px;display:flex;align-items:center;gap:8px}
.hero{position:absolute;top:110px;left:0;width:1200px;height:550px;background:linear-gradient(160deg,#2d4a72 0%,#1c2f4d 55%,#0f1b2f 100%);text-align:center;color:var(--white)}
.hero h1{font-size:42px;font-weight:800;margin-top:138px;letter-spacing:.5px}
.hero p{font-size:18px;font-weight:700;margin-top:10px}
.btn-primary{display:inline-block;background:var(--blue);color:var(--white);font-weight:700;font-size:15px;padding:13px 30px;border-radius:3px}
.hero .btn-primary{margin-top:212px}
.dots{display:flex;justify-content:center;gap:8px}
.dots span{width:12px;height:12px;border-radius:50%;border:2px solid #c9ced6}
.dots span.on{background:var(--orange);border-color:var(--orange)}
.hero .dots{margin-top:28px}
.section-title{font-size:27px;font-weight:800;color:var(--heading);text-align:center}
.section-title::after{content:"";display:block;width:70px;height:3px;background:var(--blue);margin:12px auto 0}
.about{position:absolute;top:660px;left:0;width:1200px;height:290px;padding:60px 60px 0}
.about p{font-size:13.5px;line-height:1.75;text-align:center;margin-top:22px}
.programs{position:absolute;top:950px;left:0;width:1200px;height:430px;background:var(--blue);padding-top:38px;color:var(--white)}
.programs .section-title{color:var(--white)}
.programs .section-title::after{background:var(--white)}
.program-grid{display:grid;grid-template-columns:520px 520px;column-gap:60px;row-gap:34px;margin:38px 0 0 80px}
.program{display:flex;gap:20px}
.program svg{flex:none}
.program h3{font-size:18px;font-weight:700}
.program p{font-size:12.5px;line-height:1.55;margin-top:4px;color:#dfe9f5}
.testimonials{position:absolute;top:1380px;left:0;width:1200px;height:380px;padding-top:48px;text-align:center}
.testimonials > p{width:1000px;margin:24px auto 0;font-size:13.5px;line-height:1.75;font-style:italic}
.avatar{width:74px;height:74px;border-radius:50%;background:linear-gradient(#b9a896,#6d5a4a);margin:26px auto 0}
.client-name{font-size:14px;font-weight:800;color:var(--heading);margin-top:10px}
.testimonials .dots{margin-top:14px}
.study-banner{position:absolute;top:1760px;left:0;width:1200px;height:440px;background:linear-gradient(180deg,var(--sky-top),var(--sky-bottom))}
.ribbon{position:absolute;left:360px;top:120px;width:360px;background:var(--green);color:var(--white);font-weight:800;font-size:40px;line-height:1.05;text-align:center;padding:16px 10px}
.study-banner .btn-start{position:absolute;left:368px;top:300px;background:var(--orange);color:var(--white);font-weight:700;font-size:20px;padding:16px 44px;border-radius:3px}
.student-photo{position:absolute;left:720px;top:30px;width:280px;height:410px;background:linear-gradient(180deg,#c9b7d8,#8d6fb2);border-radius:140px 140px 0 0}
.highlights{position:absolute;top:2200px;left:0;width:1200px;height:440px}
.video{position:absolute;left:80px;top:72px;width:500px;height:290px;background:linear-gradient(135deg,#5d7f98,#2b3f52)}
.video .play{position:absolute;left:210px;top:105px}
.tick-list{position:absolute;left:640px;top:84px;list-style:none}
.tick-list li{display:flex;align-items:center;gap:16px;font-size:22px;font-weight:600;color:var(--heading);height:52px}
.site-footer{position:absolute;top:2640px;left:0;width:1200px;height:308px;background:var(--navy);color:#c7d0de}
.newsletter{display:flex;align-items:center;gap:22px;padding:24px 0 0 240px}
.newsletter h4{font-size:22px;font-weight:600;color:var(--white)}
.newsletter .field{width:300px;height:36px;background:var(--white);color:#999;font-size:13px;padding:9px 14px}
.newsletter .signup{background:var(--orange);color:var(--white);font-weight:700;font-size:13px;padding:10px 22px}
.footer-cols{display:flex;padding:30px 0 0 72px;gap:0}
.footer-cols h5{font-size:13px;font-weight:700;color:var(--white);letter-spacing:.5px;margin-bottom:8px}
.footer-cols li{list-style:none;font-size:12px;line-height:1.6}
.col-info{width:160px}.col-programs{width:300px}.col-contact{width:240px}.col-follow{width:160px}
.social{display:flex;gap:8px}
.social span{width:26px;height:26px;border:1.5px solid #c7d0de;border-radius:50%}
.partner-badge{width:150px;height:60px;background:var(--white);margin-top:6px}
.copyright{position:absolute;bottom:0;left:0;width:1200px;height:42px;background:var(--navy-deep);font-size:12px;padding:13px 72px}
</style>
</head>
<body>
<header class="site-header">
  <div class="brand">
    <div class="brand-mark"></div>
    <div>
      <div class="brand-name">CORVALE</div>
      <div class="brand-sub">INSTITUTE OF BUSINESS &amp; TECHNOLOGY</div>
    </div>
  </div>
  <nav class="main-nav"><span class="active">HOME</span><span>ABOUT US</span><span>COURSES</span><span>CONTACT US</span></nav>
  <div class="phone-btn">
    <svg width="14" height="14" viewBox="0 0 24 24"><path fill="#fff" d="M6.6 10.8a15.5 15.5 0 0 0 6.6 6.6l2.2-2.2c.3-.3.7-.4 1-.2 1.1.4 2.3.6 3.6.6.6 0 1 .4 1 1V20c0 .6-.4 1-1 1A17 17 0 0 1 3 4c0-.6.4-1 1-1h3.5c.6 0 1 .4 1 1 0 1.3.2 2.5.6 3.6.1.3 0 .7-.2 1z"/></svg>
    +260 211 555 014
  </div>
</header>

<section class="hero" role="img" aria-label="Dark blue photo of a desk with a laptop keyboard and coffee cup">
  <h1>LOREM IPSUM DOLOR SIT AMET</h1>
  <p>LOREM IPSUM DOLOR SIT AMET, CONSECTETUR ADIPISCING ELIT, SED DO EIUSMOD TEMPOR.</p>
  <span class="btn-primary">LEARN MORE</span>
  <div class="dots"><span class="on"></span><span></span><span></span><span></span></div>
</section>

<section class="about">
  <h2 class="section-title">ABOUT CORVALE INSTITUTE OF BUSINESS AND TECHNOLOGY</h2>
  <p>Corvale Institute of Business and Technology (CIBT) is a fast growing Education &amp; Training Solution Provider, focusing on holistic knowledge and skills that help learners build meaningful careers. It was established on the core values of creating a rewarding and measurable difference in the careers of students, working professionals and organisations alike. CIBT prepares students not only for professional careers but also inculcates the importance of discipline, lifelong learning and personal growth. The institution is licensed and registered under the national technical education, vocational and entrepreneurship training authority.</p>
</section>

<section class="programs">
  <h2 class="section-title">PROGRAMS OFFERED</h2>
  <div class="program-grid">
    <div class="program">
      <svg width="44" height="44" viewBox="0 0 24 24"><path fill="#fff" d="M12 3 1 9l11 6 9-4.9V17h2V9zM5 13.2v4L12 21l7-3.8v-4L12 17z"/></svg>
      <div><h3>University Education – Long Distance Learning</h3><p>Flexible degree study from home with guided modules, tutor support and regular assessment sessions.</p></div>
    </div>
    <div class="program">
      <svg width="44" height="44" viewBox="0 0 24 24"><path fill="#fff" d="M9 21h6v-1H9zm3-19a7 7 0 0 0-4 12.7V17h8v-2.3A7 7 0 0 0 12 2z"/></svg>
      <div><h3>Skillbridge</h3><p>Practical career programs linking learners to industry needs and supporting job placement goals.</p></div>
    </div>
    <div class="program">
      <svg width="44" height="44" viewBox="0 0 24 24"><circle cx="8" cy="8" r="3" fill="#fff"/><circle cx="16" cy="8" r="3" fill="#fff"/><path fill="#fff" d="M2 19c0-3 3-5 6-5s6 2 6 5zm12 0c0-1.5-.5-2.8-1.4-3.8.9-.8 2.1-1.2 3.4-1.2 3 0 6 2 6 5z"/></svg>
      <div><h3>Modular Soft Skills</h3><p>Short modules in communication, teamwork and leadership designed for workplace readiness.</p></div>
    </div>
    <div class="program">
      <svg width="44" height="44" viewBox="0 0 24 24"><path fill="#fff" d="M3 21V10h4v11zm7 0V4h4v17zm7 0v-7h4v7z"/></svg>
      <div><h3>Skillbridge Roles In The Talent Continuum</h3><p>Structured pathways that guide professionals from entry level roles toward senior positions.</p></div>
    </div>
    <div class="program">
      <svg width="44" height="44" viewBox="0 0 24 24"><path fill="#fff" d="M3 5h18v11H3zm2 2v7h14V7zM8 19h8v2H8z"/></svg>
      <div><h3>Direct to Device (D2D)</h3><p>Course content delivered straight to phones, tablets and laptops for learning anywhere.</p></div>
    </div>
    <div class="program">
      <svg width="44" height="44" viewBox="0 0 24 24"><path fill="#fff" d="M9 4h6v2h5v14H4V6h5zm2 2h2V5h-2z"/></svg>
      <div><h3>Business Verticals</h3><p>Focused training in finance, marketing, management and computing for growing organisations.</p></div>
    </div>
  </div>
</section>

<section class="testimonials">
  <h2 class="section-title">WHAT OTHER SAYS TESTIMONIALS</h2>
  <p>Studying here changed the way I approach my work. The tutors were patient, the courses were practical and the computer classes gave me the confidence I needed. Within months of finishing my program I secured a better position and I now recommend the institute to friends and colleagues who want real career growth.</p>
  <div class="avatar" role="img" aria-label="Portrait of the student giving the testimonial"></div>
  <div class="client-name">ANITA</div>
  <div class="dots"><span></span><span class="on"></span><span></span><span></span></div>
</section>

<section class="study-banner" role="img" aria-label="Light sky background with a smiling student holding a laptop">
  <div class="ribbon">ONLINE STUDY RESOURCE WHICH FREE</div>
  <span class="btn-start">GET START</span>
  <div class="student-photo"></div>
</section>

<section class="highlights">
  <div class="video" role="img" aria-label="Video still of a student working at a laptop">
    <svg class="play" width="80" height="80" viewBox="0 0 80 80"><circle cx="40" cy="40" r="36" fill="none" stroke="#fff" stroke-width="4"/><path d="M32 24v32l24-16z" fill="#fff"/></svg>
  </div>
  <ul class="tick-list">
    <li><svg width="26" height="26" viewBox="0 0 26 26"><circle cx="13" cy="13" r="13" fill="#1f6db5"/><path d="M7 13.5l4 4 8-8" stroke="#fff" stroke-width="2.6" fill="none"/></svg>Lorem ipsum dolor sit amet</li>
    <li><svg width="26" height="26" viewBox="0 0 26 26"><circle cx="13" cy="13" r="13" fill="#1f6db5"/><path d="M7 13.5l4 4 8-8" stroke="#fff" stroke-width="2.6" fill="none"/></svg>Sed ut perspiciatis unde omnis iste</li>
    <li><svg width="26" height="26" viewBox="0 0 26 26"><circle cx="13" cy="13" r="13" fill="#1f6db5"/><path d="M7 13.5l4 4 8-8" stroke="#fff" stroke-width="2.6" fill="none"/></svg>Qui dolorem ipsum quia dolor sit amet</li>
    <li><svg width="26" height="26" viewBox="0 0 26 26"><circle cx="13" cy="13" r="13" fill="#1f6db5"/><path d="M7 13.5l4 4 8-8" stroke="#fff" stroke-width="2.6" fill="none"/></svg>Vel illum qui dolorem eum fugiat quo</li>
    <li><svg width="26" height="26" viewBox="0 0 26 26"><circle cx="13" cy="13" r="13" fill="#1f6db5"/><path d="M7 13.5l4 4 8-8" stroke="#fff" stroke-width="2.6" fill="none"/></svg>Nemo enim ipsam voluptatem quia</li>
  </ul>
</section>

<footer class="site-footer">
  <div class="newsletter">
    <h4>Join our email list</h4>
    <div class="field">Enter your email address</div>
    <div class="signup">SIGN UP NOW</div>
  </div>
  <div class="footer-cols">
    <div class="col-info"><h5>INFORMATION</h5><ul><li>Home</li><li>About Us</li><li>Courses</li><li>Contact Us</li></ul></div>
    <div class="col-programs"><h5>PROGRAMS OFFERED</h5><ul><li>University Education – Long Distance Learning</li><li>Modular Soft Skills</li><li>Direct To Device (D2D)</li><li>Skillbridge</li><li>Skillbridge Roles In The Talent Continuum</li><li>Business Verticals</li></ul></div>
    <div class="col-contact"><h5>CONTACT US</h5><ul><li>14 Lantern Road, Woodbrook</li><li>Harbour Park, Northgate</li><li>Tel: +260 211 555 014</li><li>E: info@corvale-edu.com</li></ul></div>
    <div class="col-follow"><h5>FOLLOW US</h5><div class="social"><span></span><span></span><span></span></div></div>
    <div class="col-partner"><h5>IN CONJUNCTION WITH SKILLBRIDGE</h5><div class="partner-badge"></div></div>
  </div>
  <div class="copyright">© 2015 Corvale Institute Of Business And Technology. All Rights Reserved</div>
</footer>
</body>
</html>
```